Zenqo - revolutionary mobile payment

The app is a P2P money trasfert, without the using of credit card or bank circuits it can transfer electronic money from one person to another consumers simply and immediatelly.
You can use the color you want, but the message we need to transert to consumer is simplicity, safety and coolness.
In attach the logo of the company and the wireframe of thre page of the app.
The goal is to design the page of the app with a clear, simple and intuitive graphic.
Updates

I have upgrade the brief with important information and detail, many thanks

Target Market(s)

all the people

Industry/Entity Type

Credit Card

Requirements
Must have
• You have to design one icon for each button in the first page, (shop is: where to shop)
in the second one a new intuitive image (instead of the hand) that let the user to understand that with a simple swipe he can process the payment
Nice to have
• You can include or esxclude what you want or belive can improve user experience of the app
Should not have
• too much color, too much button or information

```html
<!DOCTYPE html>
<html lang="it">
<head>
<meta charset="utf-8">
<title>Zenqo – Movimenti</title>
<link rel="stylesheet" href="https://fonts.googleapis.com/css2?family=Questrial&display=swap">
<style>
  :root{
    --stage:#c3c6cb;
    --ink:#111214;
    --white:#ffffff;
    --paper:#f4f4f4;
    --brand:#1f3f8f;
    --header:rgba(44,44,46,.92);
    --row:rgba(34,34,36,.9);
    --row-line:rgba(255,255,255,.08);
    --muted:#d9d9d9;
    --red:#b81f24;
    --green:#25a043;
  }
  *{box-sizing:border-box;margin:0;padding:0}
  html,body{width:1200px;height:1195px;overflow:hidden;background:var(--stage);font-family:"Questrial",sans-serif}
  .screen{position:absolute;left:300px;top:65px;width:600px;height:1065px;overflow:hidden;background:#1d1d1f;box-shadow:0 10px 40px rgba(0,0,0,.18)}
  .status-bar{position:absolute;left:0;top:0;width:100%;height:38px;background:var(--ink);color:var(--white);font-size:19px;display:flex;align-items:center;justify-content:space-between;padding:0 16px;z-index:3}
  .status-bar .carrier{display:flex;align-items:center;gap:8px}
  .dots{letter-spacing:1px;font-size:14px}
  .battery{display:flex;align-items:center;gap:8px}
  .battery-cell{width:38px;height:17px;border:2px solid var(--white);border-radius:3px;position:relative}
  .battery-cell::after{content:"";position:absolute;left:2px;top:2px;width:8px;height:9px;background:var(--white)}
  .top-bar{position:absolute;left:0;top:38px;width:100%;height:72px;background:var(--paper)}
  .settings{position:absolute;left:22px;top:24px}
  .brand{position:absolute;right:22px;top:6px;font-size:26px;line-height:30px;color:var(--brand);display:flex;align-items:center;gap:8px}
  .brand-dot{width:12px;height:12px;border-radius:50%;background:var(--brand)}
  .backdrop{position:absolute;left:0;top:110px;width:100%;height:955px;
    background:
      radial-gradient(ellipse 150px 110px at 300px 140px,rgba(240,130,40,.95),transparent 70%),
      radial-gradient(ellipse 120px 200px at 560px 330px,rgba(220,110,30,.8),transparent 70%),
      radial-gradient(ellipse 160px 120px at 90px 420px,rgba(215,105,30,.7),transparent 70%),
      radial-gradient(ellipse 200px 160px at 300px 820px,rgba(160,70,20,.55),transparent 70%),
      radial-gradient(ellipse 140px 140px at 540px 140px,rgba(200,200,190,.35),transparent 70%),
      linear-gradient(180deg,#2d2d2e 0%,#3a3836 40%,#252425 100%)}
  .header-panel{position:absolute;left:130px;top:80px;width:470px;height:180px;background:var(--header);z-index:2}
  .side-column{position:absolute;left:0;top:110px;width:130px;height:300px;background:rgba(14,14,16,.85);color:var(--white);font-size:21px;padding:150px 0 0 16px}
  .balance{position:absolute;left:70px;top:60px;color:var(--white)}
  .balance-label{font-size:22px}
  .balance-amount{font-size:42px;font-weight:700;letter-spacing:1px}
  .avatar{position:absolute;left:310px;top:8px;width:130px;height:130px;border-radius:50%;border:4px solid var(--white);background:radial-gradient(circle at 50% 45%,#9c8a72,#4d5b3a 70%)}
  .period{position:absolute;left:360px;top:226px;width:215px;height:34px;background:rgba(10,10,10,.95);color:var(--white);font-size:15px;display:flex;align-items:center;justify-content:space-between;padding:0 12px;z-index:3}
  .transactions{position:absolute;left:120px;top:272px;width:460px;list-style:none}
  .tx{height:56px;margin-bottom:12px;background:var(--row);border-top:1px solid var(--row-line);display:flex;align-items:center;padding:0 14px;color:var(--muted)}
  .tx-icon{width:26px;height:24px;flex:none}
  .tx-number{margin-left:22px;font-size:21px;letter-spacing:1px;flex:1;white-space:nowrap}
  .tx-amount{font-size:19px;font-weight:700;color:var(--white);width:70px}
  .tx-arrow{width:14px;height:16px;flex:none}
  .actions{position:absolute;left:60px;top:790px;width:520px;display:flex;gap:30px}
  .btn{flex:1;height:88px;display:flex;align-items:center;justify-content:center;color:var(--white);font-size:28px}
  .btn-report{background:var(--red)}
  .btn-pockets{background:var(--green)}
</style>
</head>
<body>
<main class="screen">
  <div class="backdrop" role="img" aria-label="Foto sfocata di un locale con luci arancioni"></div>

  <header class="status-bar">
    <span class="carrier"><span class="dots">●●●○○</span> ONDA
      <svg width="20" height="15" viewBox="0 0 20 15"><path d="M10 14 3 7a10 10 0 0 1 14 0z" fill="#fff"/></svg></span>
    <span class="time">4:21 PM</span>
    <span class="battery">22% <span class="battery-cell"></span></span>
  </header>

  <nav class="top-bar">
    <svg class="settings" width="32" height="32" viewBox="0 0 32 32" aria-label="Impostazioni">
      <g fill="#222"><circle cx="16" cy="16" r="9"/>
        <rect x="13" y="2" width="6" height="28"/><rect x="2" y="13" width="28" height="6"/>
        <rect x="13" y="2" width="6" height="28" transform="rotate(45 16 16)"/>
        <rect x="13" y="2" width="6" height="28" transform="rotate(-45 16 16)"/></g>
      <circle cx="16" cy="16" r="4" fill="#f4f4f4"/>
    </svg>
    <span class="brand"><span class="brand-dot"></span>Zenqo</span>
  </nav>

  <aside class="side-column">‹ Indietro</aside>

  <section class="header-panel">
    <div class="balance">
      <p class="balance-label">Il Tuo Saldo</p>
      <p class="balance-amount">€106.82</p>
    </div>
    <div class="avatar" role="img" aria-label="Foto profilo dell'utente"></div>
  </section>

  <div class="period">Ultimi 30 Giorni
    <svg width="12" height="8" viewBox="0 0 12 8"><path d="M1 1l5 5 5-5" stroke="#fff" stroke-width="2" fill="none"/></svg>
  </div>

  <ul class="transactions">
    <li class="tx"><svg class="tx-icon" viewBox="0 0 26 24"><path d="M13 1 1 12h4v11h6v-7h4v7h6V12h4z" fill="#fff"/></svg><span class="tx-number">+39 340 118 5093</span><span class="tx-amount">€ 1</span><svg class="tx-arrow" viewBox="0 0 14 16"><path d="M1 1l12 7-12 7z" fill="#fff"/></svg></li>
    <li class="tx"><svg class="tx-icon" viewBox="0 0 26 24"><path d="M13 1 1 12h4v11h6v-7h4v7h6V12h4z" fill="#fff"/></svg><span class="tx-number">+39 340 118 5093</span><span class="tx-amount">€ -1</span><svg class="tx-arrow" viewBox="0 0 14 16"><path d="M1 1l12 7-12 7z" fill="#fff"/></svg></li>
    <li class="tx"><svg class="tx-icon" viewBox="0 0 26 24"><path d="M13 1 1 12h4v11h6v-7h4v7h6V12h4z" fill="#fff"/></svg><span class="tx-number">+39 020 447 6138</span><span class="tx-amount">€ 200</span><svg class="tx-arrow" viewBox="0 0 14 16"><path d="M1 1l12 7-12 7z" fill="#fff"/></svg></li>
    <li class="tx"><svg class="tx-icon" viewBox="0 0 26 24"><path d="M13 1 1 12h4v11h6v-7h4v7h6V12h4z" fill="#fff"/></svg><span class="tx-number">+39 551 903 2764</span><span class="tx-amount">€ 12</span><svg class="tx-arrow" viewBox="0 0 14 16"><path d="M1 1l12 7-12 7z" fill="#fff"/></svg></li>
    <li class="tx"><svg class="tx-icon" viewBox="0 0 26 24"><path d="M13 1 1 12h4v11h6v-7h4v7h6V12h4z" fill="#fff"/></svg><span class="tx-number">+39 340 118 5093</span><span class="tx-amount">€ -1</span><svg class="tx-arrow" viewBox="0 0 14 16"><path d="M1 1l12 7-12 7z" fill="#fff"/></svg></li>
    <li class="tx"><svg class="tx-icon" viewBox="0 0 26 24"><path d="M13 1 1 12h4v11h6v-7h4v7h6V12h4z" fill="#fff"/></svg><span class="tx-number">+39 020 447 6138</span><span class="tx-amount">€ 200</span><svg class="tx-arrow" viewBox="0 0 14 16"><path d="M1 1l12 7-12 7z" fill="#fff"/></svg></li>
    <li class="tx"><svg class="tx-icon" viewBox="0 0 26 24"><path d="M13 1 1 12h4v11h6v-7h4v7h6V12h4z" fill="#fff"/></svg><span class="tx-number">+39 551 903 2764</span><span class="tx-amount">€ 12</span><svg class="tx-arrow" viewBox="0 0 14 16"><path d="M1 1l12 7-12 7z" fill="#fff"/></svg></li>
  </ul>

  <div class="actions">
    <a class="btn btn-report">Report</a>
    <a class="btn btn-pockets">Tasche</a>
  </div>
</main>
</body>
</html>
```